Wall art for an Investments Lab at a college

Wall art for inside a new investments lab. A photo of the lab is attached. The wall art will go on the wall in the back right (pictured). It is currently white and the adjacent walls are white. The accent wall in the room is blue (summer nights). A copy of our color palette for environmental design is also attached. The tag line should be INVESTING IN THE FUTURE.

Target Market(s)

College students

Industry/Entity Type

Finance

Requirements
Must have
• Incorporate colors from palette

```html
<!DOCTYPE html>
<html lang="en">
<head>
<meta charset="utf-8">
<title>Investing in the Future — Wall Art</title>
<link rel="stylesheet" href="https://fonts.googleapis.com/css2?family=Big+Shoulders+Stencil+Display:wght@500&display=swap">
<style>
  :root {
    --wall-light: #537f9b;
    --wall-mid: #47718f;
    --wall-dark: #145171;
    --ink: #ffffff;
  }
  html, body {
    margin: 0;
    padding: 0;
    width: 1200px;
    height: 927px;
    overflow: hidden;
  }
  .wall-art {
    position: relative;
    width: 1200px;
    height: 927px;
    background: linear-gradient(90deg, var(--wall-light) 0%, var(--wall-light) 20%, var(--wall-mid) 50%, var(--wall-dark) 100%);
  }
  .tagline-panel {
    position: absolute;
    left: 0;
    top: 0;
    width: 1200px;
    height: 927px;
  }
  .tagline-frame {
    fill: none;
    stroke: var(--ink);
    stroke-width: 6;
  }
  .tagline {
    font-family: "Big Shoulders Stencil Display", "Arial Narrow", sans-serif;
    font-weight: 500;
    font-size: 88px;
    fill: var(--ink);
  }
</style>
</head>
<body>
  <main class="wall-art">
    <svg class="tagline-panel" viewBox="0 0 1200 927" xmlns="http://www.w3.org/2000/svg">
      <rect class="tagline-frame" x="92" y="170" width="1005" height="144"/>
      <text class="tagline" x="124" y="276" textLength="953" lengthAdjust="spacingAndGlyphs">INVESTING IN THE FUTURE.</text>
    </svg>
  </main>
</body>
</html>
```